Graphic Design for a 3 Banner Tradeshow Setup

We are a Pipe Restoration company that specializes in trenchless pipelining. We need a design for a 3 banner setup to use at tradeshows. See attached "banner specs" for sizing - note the 48" x 92" will be in between the two 36" x 92" banners. See attached "Mock-Up" of information each banner needs and utilize the color scheme of the banners we already have in the "both DWM banners" AI file attached. The final designs should communicate what we do and attract people into our booth. We would like to have graphics of realistic pipes for a before (dirty pipe), after cleaning pipe, and lined pipe - see example of "pipe pictures" attached. I'm not sure if this is something you can generate or if we will need to find images of our own to send. Also, see attached "screenshot-process" to see similar images we would like to use to showcase the process.
Target Market(s)
Homeowners, Property Managers, HOA Communities, Healthcare Facilities & Hospitals, and commercial properties
Industry/Entity Type
Trenchless Pipelining
Look and feel

```html
<!DOCTYPE html>
<html lang="en">
<head>
<meta charset="utf-8">
<title>DWM Tradeshow Banners</title>
<link rel="stylesheet" href="https://fonts.googleapis.com/css2?family=Poppins:wght@400;500;700;800;900&family=Roboto+Condensed:wght@400;700;800&display=swap">
<style>
:root{
  --page:#e4e3e5;
  --blue-top:#1b63a6;
  --blue-mid:#16508f;
  --blue-deep:#112f6b;
  --cyan:#00aee6;
  --cyan-btn:#1d94d2;
  --ink:#1c1c1c;
  --navy-text:#1c3f7a;
  --white:#ffffff;
}
*{margin:0;padding:0;box-sizing:border-box}
html,body{width:1200px;height:954px;overflow:hidden;background:var(--page)}
body{position:relative;font-family:"Poppins",sans-serif;color:var(--white)}

.banner{position:absolute;top:103px;height:690px;overflow:hidden;
  background:linear-gradient(180deg,#ffffff 60%,#e9ecef 100%);
  box-shadow:0 8px 14px rgba(0,0,0,.18)}
.banner--assess{left:70px;width:270px}
.banner--problems{left:407px;width:367px}
.banner--fix{left:857px;width:270px}

.banner__shape{position:absolute;left:0;top:0;width:100%;height:100%}

.line{position:absolute;left:0;right:0;text-align:center;white-space:nowrap}

.brand{position:absolute;left:0;right:0;top:28px;text-align:center}
.brand__name{display:inline-flex;align-items:center;gap:6px;font-weight:800;font-size:38px;line-height:1;letter-spacing:3px;color:var(--white)}
.brand__mark{width:14px;height:14px;background:var(--white);display:inline-block}
.brand__tag{display:block;margin-top:6px;font-size:8px;font-weight:500;letter-spacing:2.4px;color:var(--white)}

.headline{font-weight:900;line-height:1;color:var(--white);letter-spacing:-.5px}

.feature{position:absolute;width:90px;transform:translateX(-50%);text-align:center}
.feature svg{display:block;margin:0 auto 6px;width:38px;height:38px}
.feature__label{font-size:11px;font-weight:700;line-height:1.25;color:var(--white)}

.divider-v{position:absolute;border-left:1px dashed rgba(255,255,255,.35)}
.divider-h{position:absolute;border-top:1px dashed rgba(255,255,255,.35)}

.contact__call{font-weight:500;letter-spacing:4px;color:var(--navy-text)}
.contact__phone{font-family:"Roboto Condensed",sans-serif;font-weight:800;color:var(--ink);letter-spacing:-.5px;line-height:1}
.contact__web{position:absolute;background:var(--cyan-btn);color:var(--white);
  font-family:"Roboto Condensed",sans-serif;display:flex;align-items:center;justify-content:center;box-shadow:0 4px 6px rgba(0,0,0,.15)}
.contact__web b{font-weight:800}

.photo{position:absolute;border:1px solid var(--white)}

.pitch{font-size:21.5px;line-height:29px}
.pitch--accent{color:var(--cyan);font-weight:800}
.pitch--plain{color:var(--white);font-weight:500}
</style>
</head>
<body>

<!-- Left banner: assessment services -->
<section class="banner banner--assess">
  <svg class="banner__shape" viewBox="0 0 270 690" preserveAspectRatio="none" aria-hidden="true">
    <defs>
      <linearGradient id="blueA" x1="0" y1="0" x2="0" y2="1">
        <stop offset="0" stop-color="#1b63a6"/><stop offset=".5" stop-color="#16508f"/><stop offset="1" stop-color="#112f6b"/>
      </linearGradient>
    </defs>
    <polygon points="0,0 270,0 270,444 135,524 0,444" fill="url(#blueA)"/>
    <polygon points="50,478 135,528 217,478 217,496 135,546 50,496" fill="#222"/>
  </svg>

  <div class="brand"><span class="brand__name"><i class="brand__mark"></i>DWM</span><span class="brand__tag">DWM PIPE WORKS</span></div>

  <div class="line headline" style="top:106px;font-size:50px">WE</div>
  <div class="line headline" style="top:156px;font-size:56px">ASSESS</div>

  <div class="divider-v" style="left:137px;top:248px;height:216px"></div>
  <div class="divider-h" style="left:32px;top:354px;width:94px"></div>
  <div class="divider-h" style="left:146px;top:354px;width:94px"></div>

  <div class="feature" style="left:76px;top:250px">
    <svg viewBox="0 0 40 40"><rect x="8" y="6" width="26" height="13" rx="2" fill="var(--cyan)" transform="rotate(18 21 12)"/><circle cx="29" cy="16" r="3" fill="#fff"/><rect x="14" y="20" width="4" height="10" fill="#fff"/><rect x="4" y="26" width="3" height="12" fill="#fff"/><rect x="4" y="30" width="12" height="3" fill="#fff"/></svg>
    <div class="feature__label">CCTV Pipe Investigation</div>
  </div>
  <div class="feature" style="left:193px;top:250px">
    <svg viewBox="0 0 40 40"><circle cx="24" cy="20" r="14" fill="#fff"/><path d="M24 20 L24 6 A14 14 0 0 1 38 20 Z" fill="var(--cyan)"/><path d="M26 22 L40 22 A14 14 0 0 1 34 33 Z" fill="var(--cyan)"/><circle cx="10" cy="15" r="6" fill="var(--blue-mid)" stroke="#fff" stroke-width="2"/><rect x="4" y="24" width="12" height="3" fill="#fff"/><rect x="4" y="29" width="12" height="3" fill="#fff"/><rect x="4" y="34" width="12" height="3" fill="#fff"/></svg>
    <div class="feature__label">Budgetary Evaluation</div>
  </div>
  <div class="feature" style="left:76px;top:368px">
    <svg viewBox="0 0 40 40"><rect x="3" y="2" width="16" height="22" fill="var(--cyan)"/><rect x="6" y="7" width="10" height="2" fill="#fff"/><rect x="6" y="12" width="10" height="2" fill="#fff"/><rect x="6" y="17" width="8" height="2" fill="#fff"/><circle cx="20" cy="32" r="6" fill="#fff"/><circle cx="33" cy="32" r="6" fill="#fff"/><rect x="18" y="20" width="4" height="10" fill="#fff"/><rect x="31" y="20" width="4" height="10" fill="#fff"/></svg>
    <div class="feature__label">Scope Development</div>
  </div>
  <div class="feature" style="left:193px;top:368px">
    <svg viewBox="0 0 40 40"><circle cx="17" cy="18" r="10" fill="#fff"/><rect x="13" y="28" width="8" height="6" fill="#fff"/><circle cx="29" cy="11" r="7" fill="var(--cyan)"/><circle cx="29" cy="11" r="3" fill="var(--blue-mid)"/><circle cx="11" cy="30" r="4" fill="var(--cyan)"/></svg>
    <div class="feature__label" style="margin-top:3px">Project Oversight</div>
  </div>

  <div class="line contact__call" style="top:570px;font-size:13px">CONTACT US NOW!</div>
  <div class="line contact__phone" style="top:589px;font-size:31px">1-800-555-0148</div>
  <div class="contact__web" style="left:23px;top:626px;width:219px;height:22px;font-size:13px">www.<b>dwmpipeworks</b>.com</div>
</section>

<!-- Center banner: pipe problems -->
<section class="banner banner--problems">
  <svg class="banner__shape" viewBox="0 0 367 690" preserveAspectRatio="none" aria-hidden="true">
    <defs>
      <linearGradient id="blueB" x1="0" y1="0" x2="0" y2="1">
        <stop offset="0" stop-color="#1b63a6"/><stop offset=".5" stop-color="#16508f"/><stop offset="1" stop-color="#112f6b"/>
      </linearGradient>
    </defs>
    <polygon points="0,0 39,0 39,122 0,144" fill="var(--cyan)"/>
    <polygon points="328,0 367,0 367,133 328,111" fill="var(--cyan)"/>
    <polygon points="42,0 325,0 325,440 183,524 42,440" fill="url(#blueB)"/>
    <polygon points="98,478 183,528 266,478 266,496 183,546 98,496" fill="#222"/>
  </svg>

  <div class="brand"><span class="brand__name"><i class="brand__mark"></i>DWM</span><span class="brand__tag">DWM PIPE WORKS</span></div>

  <div class="line headline" style="top:107px;font-size:50px">PIPE</div>
  <div class="line headline" style="top:152px;font-size:40px">PROBLEMS?</div>

  <div class="photo" role="img" aria-label="Row of pipe sections: corroded dirty pipe, cleaned pipe and lined pipes"
       style="left:55px;top:223px;width:251px;height:46px;border:none;border-radius:23px;
       background:linear-gradient(90deg,#7a4a2a 0%,#9a6238 30%,#3fb6d4 44%,#5a5a5a 60%,#7a8a80 75%,#3d3d3d 88%,#b04228 100%)"></div>

  <div class="line pitch pitch--accent" style="top:296px">WE HELP FIX PIPE</div>
  <div class="line pitch pitch--accent" style="top:325px">PROBLEMS</div>
  <div class="line pitch pitch--plain" style="top:354px">WITHOUT HAVING</div>
  <div class="line pitch pitch--plain" style="top:383px">TO TEAR UP YOUR</div>
  <div class="line pitch pitch--plain" style="top:412px">BUIDLING</div>

  <div class="line contact__call" style="top:555px;font-size:18px;letter-spacing:5px">CONTACT US NOW!</div>
  <div class="line contact__phone" style="top:578px;font-size:41px">1-800-555-0148</div>
  <div class="contact__web" style="left:32px;top:627px;width:297px;height:30px;font-size:18px">www.<b>dwmpipeworks</b>.com</div>
</section>

<!-- Right banner: fix services -->
<section class="banner banner--fix">
  <svg class="banner__shape" viewBox="0 0 270 690" preserveAspectRatio="none" aria-hidden="true">
    <defs>
      <linearGradient id="blueC" x1="0" y1="0" x2="0" y2="1">
        <stop offset="0" stop-color="#1b63a6"/><stop offset=".5" stop-color="#16508f"/><stop offset="1" stop-color="#112f6b"/>
      </linearGradient>
    </defs>
    <polygon points="0,0 270,0 270,444 135,524 0,444" fill="url(#blueC)"/>
    <polygon points="51,478 135,528 217,478 217,496 135,546 51,496" fill="#222"/>
  </svg>

  <div class="brand"><span class="brand__name"><i class="brand__mark"></i>DWM</span><span class="brand__tag">DWM PIPE WORKS</span></div>

  <div class="line headline" style="top:106px;font-size:54px">WE FIX</div>

  <div class="photo" role="img" aria-label="Technician running a pipe inspection camera" style="left:25px;top:173px;width:73px;height:54px;background:linear-gradient(135deg,#8a7a66,#2f5fa8)"></div>
  <div class="photo" role="img" aria-label="Technician mixing lining resin" style="left:101px;top:173px;width:71px;height:54px;background:linear-gradient(135deg,#6f8aa3,#2a7ec8)"></div>
  <div class="photo" role="img" aria-label="Crew installing a pipe liner" style="left:176px;top:173px;width:71px;height:54px;background:linear-gradient(135deg,#8c8c88,#2d56a0)"></div>

  <div class="divider-v" style="left:89px;top:262px;height:180px"></div>
  <div class="divider-v" style="left:185px;top:262px;height:180px"></div>
  <div class="divider-h" style="left:20px;top:352px;width:60px"></div>
  <div class="divider-h" style="left:100px;top:350px;width:74px"></div>
  <div class="divider-h" style="left:193px;top:349px;width:58px"></div>

  <div class="feature" style="left:52px;top:262px">
    <svg viewBox="0 0 40 40"><rect x="4" y="2" width="5" height="16" fill="#fff"/><rect x="11" y="2" width="5" height="16" fill="#fff"/><path d="M18 4 h6 a10 10 0 0 1 10 10 v4 h-6 v-4 a4 4 0 0 0 -4 -4 h-6z" fill="var(--cyan)"/><path d="M2 26 q5 -4 9 0 t9 0 t9 0 t9 0 v12 h-36z" fill="var(--cyan)"/></svg>
    <div class="feature__label">Slow Drains</div>
  </div>
  <div class="feature" style="left:134px;top:262px">
    <svg viewBox="0 0 40 40"><rect x="6" y="4" width="10" height="6" fill="#fff"/><rect x="9" y="10" width="5" height="26" fill="#fff"/><rect x="23" y="2" width="12" height="4" fill="var(--cyan)"/><rect x="25" y="6" width="8" height="30" fill="var(--cyan)"/><rect x="23" y="34" width="12" height="4" fill="var(--cyan)"/><circle cx="29" cy="18" r="3" fill="var(--blue-mid)"/></svg>
    <div class="feature__label">Back-Ups</div>
  </div>
  <div class="feature" style="left:221px;top:262px">
    <svg viewBox="0 0 40 40"><path d="M20 6 L34 16 V34 H6 V16z" fill="var(--cyan)"/><rect x="17" y="16" width="6" height="18" fill="#fff"/><rect x="4" y="34" width="32" height="3" fill="#fff"/><rect x="4" y="4" width="8" height="2" fill="#fff"/><rect x="28" y="4" width="8" height="2" fill="#fff"/></svg>
    <div class="feature__label">Sewer Odors</div>
  </div>
  <div class="feature" style="left:52px;top:360px">
    <svg viewBox="0 0 40 40"><rect x="18" y="2" width="12" height="26" fill="var(--cyan)"/><rect x="4" y="18" width="20" height="10" fill="var(--cyan)"/><path d="M16 22 l4 3 -3 3 4 4" stroke="#fff" stroke-width="2" fill="none"/><path d="M26 32 l8 0 M30 28 l0 8" stroke="#fff" stroke-width="2"/></svg>
    <div class="feature__label">Cracked Pipes</div>
  </div>
  <div class="feature" style="left:134px;top:360px">
    <svg viewBox="0 0 40 40"><path d="M6 6 h20 v6 h-12 v8 h-8z" fill="var(--cyan)"/><circle cx="10" cy="28" r="3" fill="#fff"/><path d="M18 18 l14 14" stroke="#fff" stroke-width="5" stroke-linecap="round"/><circle cx="18" cy="18" r="5" fill="#fff"/></svg>
    <div class="feature__label">Recurring Plumbing Problems</div>
  </div>
  <div class="feature" style="left:221px;top:360px">
    <svg viewBox="0 0 40 40"><circle cx="24" cy="16" r="11" fill="none" stroke="var(--cyan)" stroke-width="4"/><path d="M17 14 q7 -4 14 2 M20 20 q5 -2 8 3" stroke="#fff" stroke-width="2" fill="none"/><path d="M15 25 L4 36" stroke="var(--cyan)" stroke-width="5" stroke-linecap="round"/><circle cx="8" cy="8" r="4" fill="#fff"/></svg>
    <div class="feature__label">Root Intrusion</div>
  </div>

  <div class="line contact__call" style="top:570px;font-size:13px">CONTACT US NOW!</div>
  <div class="line contact__phone" style="top:589px;font-size:31px">1-800-555-0148</div>
  <div class="contact__web" style="left:23px;top:626px;width:219px;height:22px;font-size:13px">www.<b>dwmpipeworks</b>.com</div>
</section>

</body>
</html>
```